Community Management Company in need of WordPress templates for website redesign

We are a community association management company providing services to homeowner associations (HOAs), condominium associations, cooperatives, municipal utility districts, luxury high-rises and large master-planned communities within the Real Estate category.

We are looking to do a refresh of our site with newly-designed pages that are compatible with WordPress and can be uploaded to a domain with little complications.

We are interested in first having a landing page designed based on a specific audience and call to actions as described in the design brief file attached to this design project and pasted below:
Design Brief for HavenStead Website Refresh

General Details:
Company Name: HavenStead
Business Location: Carrollton, TX – HQ
Current website: www.havenstead-example.com

Overview:

We are looking to for a refresh of our site with newly-designed pages that are compatible with WordPress and can be uploaded to a domain with little complications.

Our target audience / target market:
HOA and Association Board Members, Real Estate Builders & Developers, Residents and Homeowners, Vendors, Potential Business Partners

Project scope:
Create a landing page template with the target audience of HOA Board Members who are prospects of HavenStead
The goal of the landing page is to have them fill out the proposal form by having the page take them from our “why” message to our “how” and “what” messages so they are compelled to fill out the form. The new landing page needs to drive that behavior.
Our messages will include the following

Why messages:
• Because you deserve an exceptional community
• Because you and your residents deserve an exceptional lifestyle
• Because your community matters
• Because your residents matter
• Exceptional Community. Managed
• Exceptional Lifestyle. Delivered
How/What messages:

With over 25 years of experience, HavenStead provides exceptional community management solutions with the transparency and visibility your community deserves. Our fully integrated services are provided at competitive prices with the best people, best practices, and best cloud-based and mobile app technology.

Our team is made up of the industry’s leading experts equipped to answer your questions quickly. Our team includes: certified managers, degreed and certified accountants, experienced, multi-lingual customer service representatives, technology staff and industry executives. We perform industry leading best practices, on behalf of the communities we serve, ensuring you receive the highest level support, guidance and tools to assist in performing your fiduciary duties. With our proprietary, cloud-based and mobile app technology, pertinent community information is at your fingertips. You will be empowered to manage the business affairs of your community anytime, from any device, anywhere.

Our community management services include personalized onsite management, portfolio management, full-service community maintenance services, community management for builders and property developers, and Virtual CAM (Community Association Manager) management.

Our community communication services include cloud-based board, resident, closing, and attorney portals and mobile app technology, providing the transparency and visibility into the business affairs that your community deserves. In addition, we provide several communication tools to keep homeowners and residents informed via our community website, newsletter and event services.

HavenStead, one of the largest and fastest growing community management companies, is proud to provide exceptional services to hundreds of community associations from under 50 units to over 7,000 units in Arizona, California, Colorado, Florida, Georgia, Louisiana, Nevada, North Carolina, Oregon, Texas and Washington, including homeowner associations (HOAs), condominium associations, cooperatives, luxury high-rises, municipal utility districts and large master-planned communities.

Other page elements: additional content block/placeholders for:
• Link to Service description and technology pages
• Link to Mobile Apps page
• Request a proposal form fill content block
• Find an office form fill content block and link to local page upon completion of search via zip or state
• Contact us content block with information to include phone, email, fax, etc. and link to contact us landing page

Template Elements:
Files will also be uploaded including:
• Logo
• Colors
• Sales PPT for their reference

Please see attached design brief (file #4), logos (file #2&3), colors & branding standards (file #5) and a sales PPT deck (file #1) geared towards the audience for your reference.
Updates

Reason: I am extending the deadline by one week to give everyone a chance to provide updates based on the feedback and submissions. Thank you for all of your efforts. I look forward to seeing all of your designs.

Reason: Good day everyone, We are extending our deadline by one more week; so please continue to submit your designs and revisions. We look forward to seeing your work. Regards.

Thank you for all of your submissions.  I am in the process of getting votes tallied and should have some further information Tuesday of next week.

I am currently reviewing the votes and comments from the poll and will provide feedback within the next day; so please stay tuned.

We are conducting one more round of voting for the website refresh.  Once this is complete we will contact the finalists and make a selection shortly thereafter.  Thank you again for your participation.  Please stay tuned.

We are finalizing our 2nd poll and will request revisions, if appropriate.  Thank you.

Target Market(s)

HOA Board members per the design brief

Industry/Entity Type

Communication

Requirements
Must have
• focus on a landing page first; not the homepage design
Nice to have
• Please see design brief - File #4
Should not have
• home page elements for the time being.

```html
<!DOCTYPE html>
<html lang="en">
<head>
<meta charset="utf-8">
<title>HavenStead – Community Management</title>
<link href="https://fonts.googleapis.com/css2?family=Roboto:wght@400;500;700&family=Open+Sans:wght@400;600;700&display=swap" rel="stylesheet">
<style>
  :root{
    --green-top:#4d7a2a;
    --green:#4a7a2c;
    --teal:#0f6c86;
    --teal-mid:#1a7a92;
    --cyan:#1ec8f0;
    --heading-teal:#1c6e8c;
    --text:#555;
    --red:#d42a1a;
    --panel:#f2f2f2;
    --footer:#2b2b2b;
    --footer-bottom:#1b1b1b;
    --footer-text:#9a9a9a;
    --link-cyan:#2bb7d6;
    --office-title:#0d2430;
  }
  *{margin:0;padding:0;box-sizing:border-box}
  html,body{width:1011px;height:1200px;overflow:hidden;background:#fff}
  body{position:relative;font-family:'Roboto',Arial,sans-serif;color:var(--text)}
  .abs{position:absolute}

  .top-strip{left:0;top:0;width:1011px;height:7px;background:var(--green-top)}
  .header{left:0;top:7px;width:1011px;height:76px;background:#fff}
  .brand{left:167px;top:30px;font-size:30px;font-weight:500;color:var(--green);letter-spacing:-.3px}
  .brand-sub{left:238px;top:66px;font-size:7px;color:var(--teal);letter-spacing:.4px;font-weight:500}
  .tagline{left:677px;top:30px;font-size:12px;font-style:italic;font-weight:500;color:var(--teal);line-height:11px}
  .tagline span{display:block}
  .tagline .t2{padding-left:52px;font-size:9.5px;color:#2c4a10}
  .tagline .t3{padding-left:73px}

  .nav{left:0;top:83px;width:1011px;height:40px;background:var(--teal)}
  .nav ul{list-style:none;display:flex;position:absolute;left:169px;top:0;height:40px}
  .nav li{height:40px;line-height:40px;font-size:9.3px;font-weight:500;color:#fff;padding:0 16px;white-space:nowrap}
  .nav li.active{background:var(--green);padding:0 14px 0 16px}

  .hero{left:0;top:123px;width:1011px;height:339px;background:linear-gradient(100deg,#c9b8a4 0%,#d8c9b5 25%,#e9dccd 45%,#bfd2e0 70%,#a9c2d6 100%)}
  .caption{left:168px;top:195px;width:368px;height:127px;background:rgba(90,90,90,.72)}
  .caption h1{position:absolute;left:13px;top:11px;font-size:24px;font-weight:500;color:var(--cyan)}
  .caption p{position:absolute;left:13px;top:52px;width:350px;font-size:13.6px;line-height:24px;color:#fff}
  .btn{top:331px;width:128px;height:37px;border-radius:4px;color:#fff;font-size:12.5px;text-align:center;line-height:37px}
  .btn-quote{left:168px;background:var(--green)}
  .btn-action{left:311px;background:var(--teal-mid)}
  .arrow{top:265px}
  .dots{left:487px;top:443px;display:flex;gap:5px}
  .dots i{display:block;width:9px;height:9px;border-radius:50%;border:1.5px solid #fff}
  .dots i.on{background:var(--green);border-color:var(--green)}

  .panel{left:0;top:654px;width:1011px;height:261px;background:var(--panel)}
  .welcome{left:167px;top:480px;font-size:16.5px;font-weight:400;color:var(--heading-teal)}
  .intro{left:168px;top:511px;width:676px}
  .intro p{font-size:8.2px;line-height:16.2px;letter-spacing:-.05px;color:var(--text);margin-bottom:16.2px}

  .clients-title{left:168px;top:837px;font-size:12.5px;font-weight:400;color:var(--green)}
  .clients-rule{left:297px;top:847px;width:323px;height:1px;background:#bbb}
  .clients-dots{left:626px;top:844px;display:flex;gap:2px}
  .clients-dots i{display:block;width:8px;height:8px;border-radius:50%;border:1px solid #444}
  .clients-dots i.on{background:var(--teal);border-color:var(--teal)}
  .avatar{width:64px;height:62px;border-radius:50%;background:linear-gradient(135deg,#8a7060,#c9b4a4);border:3px solid #cfcfcf}
  .quote{width:160px}
  .quote h3{font-size:8.2px;font-weight:400;color:var(--red);margin-bottom:4px}
  .quote p{font-size:8.2px;line-height:12px;color:#555}

  .office{left:662px;top:835px;width:180px;height:110px;background:var(--teal);border:1px solid #0a5468;color:#fff}
  .office h4{position:absolute;left:10px;top:9px;font-size:10px;font-weight:400;color:var(--office-title);white-space:nowrap}
  .office p{position:absolute;left:10px;top:27px;width:160px;font-size:8.3px;line-height:12px}
  .office label{position:absolute;left:11px;top:59px;font-size:10px}
  .office .field{position:absolute;left:59px;top:57px;width:107px;height:19px;background:#fff}
  .office .send{position:absolute;left:129px;top:83px;width:34px;height:16px;background:var(--green);font-size:8.5px;text-align:center;line-height:16px;border:1px solid #2d5016}

  .footer{left:0;top:968px;width:1011px;height:169px;background:var(--footer);font-family:'Open Sans',Arial,sans-serif}
  .fcol{top:0}
  .fcol h5{position:absolute;top:15px;font-size:10.2px;font-weight:700;color:#eee;white-space:nowrap}
  .flist{position:absolute;top:42px;list-style:none;white-space:nowrap}
  .flist li{font-size:8.6px;color:var(--footer-text);line-height:20px}
  .flist abbr{text-decoration:underline;text-decoration-style:dotted}
  .office-info{position:absolute;top:40px;font-size:8.8px;color:#ccc;line-height:17.5px}
  .office-info .row{position:relative;padding-left:20px;margin-bottom:11px}
  .office-info svg{position:absolute;left:0;top:4px}
  .tweet{font-size:7.3px;color:var(--footer-text);line-height:12px;margin-bottom:12px;width:200px}
  .tweet a{color:var(--link-cyan);text-decoration:none}
  .tweet em{display:block;font-size:6.4px;color:#777}

  .bottom{left:0;top:1137px;width:1011px;height:63px;background:var(--footer-bottom)}
  .copy{left:168px;top:24px;font-size:9.5px;color:#eee;white-space:nowrap}
  .social{left:755px;top:14px;display:flex;gap:7px}
  .social i{display:block;width:24px;height:24px;border-radius:50%;background:#ddd;border:2px solid #9a9a9a}
</style>
</head>
<body>
  <div class="abs top-strip"></div>
  <header class="abs header"></header>
  <div class="abs brand">HavenStead</div>
  <div class="abs brand-sub">POWERED BY NESTLINK</div>
  <div class="abs tagline"><span>Comprehensive</span><span class="t2">community management</span><span class="t3">solutions</span></div>

  <nav class="abs nav">
    <ul>
      <li class="active">Request A Proposal</li>
      <li>About Us</li>
      <li>Services</li>
      <li>Resident Service</li>
      <li>Lot/Home Sale Service</li>
      <li>Vendor Service</li>
      <li>Join Our Team</li>
      <li>Blog</li>
    </ul>
  </nav>

  <section class="abs hero" role="img" aria-label="Photo of a smiling family: father with two young children"></section>
  <div class="abs caption">
    <h1>HavenStead</h1>
    <p>Because you and your residents deserve an exceptional lifestyle</p>
  </div>
  <div class="abs btn btn-quote">Client Quote</div>
  <div class="abs btn btn-action">Call To Action</div>
  <svg class="abs arrow" style="left:52px" width="16" height="28" viewBox="0 0 16 28"><path d="M13 2 L3 14 L13 26" fill="none" stroke="#0f6c86" stroke-width="5"/></svg>
  <svg class="abs arrow" style="left:948px;top:267px" width="16" height="28" viewBox="0 0 16 28"><path d="M3 2 L13 14 L3 26" fill="none" stroke="#0f6c86" stroke-width="5"/></svg>
  <div class="abs dots"><i class="on"></i><i></i><i></i></div>

  <div class="abs panel"></div>
  <h2 class="abs welcome">Welcome to HavenStead</h2>
  <div class="abs intro">
    <p>With over 25 years of experience, HavenStead provides exceptional community management solutions with the transparency and visibility your community deserves. Our fully integrated services are provided at competitive prices with the best people, best practices, and best cloud-based and mobile app technology.</p>
    <p>Our team is made up of the industry’s leading experts equipped to answer your questions quickly. Our team includes: certified managers, degreed and certified accountants, experienced, multi-lingual customer service representatives, technology staff and industry executives. We perform industry leading best practices, on behalf of the communities we serve, ensuring you receive the highest level support, guidance and tools to assist in performing your fiduciary duties. With our proprietary, cloud-based and mobile app technology, pertinent community information is at your fingertips. You will be empowered to manage the business affairs of your community anytime, from any device, anywhere.</p>
    <p>Our community management services include personalized onsite management, portfolio management, full-service community maintenance services, community management for builders and property developers, and Virtual CAM (Community Association Manager) management.</p>
    <p>Our community communication services include cloud-based board, resident, closing, and attorney portals and mobile app technology, providing the transparency and visibility into the business affairs that your community deserves. In addition, we provide several communication tools to keep homeowners and residents informed via our community website, newsletter and event services.</p>
    <p>HavenStead, one of the largest and fastest growing community management companies, is proud to provide exceptional services to hundreds of community associations from under 50 units to over 7,000 units in Arizona, California, Colorado, Florida, Georgia, Louisiana, Nevada, North Carolina, Oregon, Texas and Washington, including homeowner associations (HOAs), condominium associations, cooperatives, luxury high-rises, municipal utility districts and large master-planned communities.</p>
  </div>

  <h3 class="abs clients-title">What Our Clients Say</h3>
  <div class="abs clients-rule"></div>
  <div class="abs clients-dots"><i class="on"></i><i></i><i></i></div>

  <div class="abs avatar" style="left:169px;top:872px" role="img" aria-label="Client portrait"></div>
  <div class="abs quote" style="left:247px;top:874px">
    <h3>Lorem ipsum dolor sit amet</h3>
    <p>Lorem ipsum dolor sit amet, consetetur sadipscing elitr, sed diam nonumy eirmod tempor invidunt</p>
  </div>
  <div class="abs avatar" style="left:421px;top:868px" role="img" aria-label="Client portrait"></div>
  <div class="abs quote" style="left:504px;top:874px">
    <h3>Lorem ipsum dolor sit amet</h3>
    <p>Lorem ipsum dolor sit amet, consetetur sadipscing elitr, sed diam nonumy eirmod tempor invidunt</p>
  </div>

  <aside class="abs office">
    <h4>Find &nbsp;a HavenStead Office</h4>
    <p>Find a HavenStead office nearest you by entering your zip code below</p>
    <label>Zip Code :</label>
    <div class="field"></div>
    <div class="send">Send</div>
  </aside>

  <footer class="abs footer">
    <div class="abs fcol" style="left:172px">
      <h5>COMPANY</h5>
      <ul class="flist"><li>Site Template</li><li>Theme Library</li><li>Blog</li><li>Forum</li><li>Wiki</li></ul>
    </div>
    <div class="abs fcol" style="left:290px">
      <h5>META</h5>
      <ul class="flist"><li>Log in</li><li>Entries <abbr>RSS</abbr></li><li>Comments <abbr>RSS</abbr></li><li>Platform.org</li></ul>
    </div>
    <div class="abs fcol" style="left:409px">
      <h5>HEAD OFFICE</h5>
      <div class="office-info" style="width:210px">
        <div class="row"><svg width="8" height="10" viewBox="0 0 8 10"><path d="M4 0a3.5 3.5 0 0 0-3.5 3.5C.5 6 4 10 4 10s3.5-4 3.5-6.5A3.5 3.5 0 0 0 4 0zm0 5a1.4 1.4 0 1 1 0-2.8A1.4 1.4 0 0 1 4 5z" fill="#ccc"/></svg>410 Elm Crossing Drive, Carrollton,<br>TX 75006</div>
        <div class="row"><svg width="9" height="9" viewBox="0 0 9 9"><rect width="9" height="9" rx="1.5" fill="#ccc"/><path d="M2.5 2c.5 2.5 2 4 4.5 4.6l.4-1-1.2-.6-.6.6C4.6 5.1 3.9 4.4 3.4 3.4l.6-.6-.6-1.2z" fill="#2b2b2b"/></svg>(555) 014-2025<br>(555) 014-2027</div>
        <div class="row"><svg width="10" height="8" viewBox="0 0 10 8"><rect x=".5" y=".5" width="9" height="7" fill="none" stroke="#ccc"/><path d="M.5 .8 5 4.5 9.5.8" fill="none" stroke="#ccc"/></svg>info@brookfold-example.com</div>
      </div>
    </div>
    <div class="abs fcol" style="left:646px">
      <h5>LATEST TWEETS</h5>
      <div class="abs" style="top:43px">
        <div class="tweet">Site Template | Site Theme | Creative Website | Brookfold <a>http://lnk.example/a7Qm2</a><em>about 5 hours ago</em></div>
        <div class="tweet">Lakeview Row <a>http://lnk.example/k3Zp9</a><em>about 1 day ago</em></div>
      </div>
    </div>
  </footer>

  <div class="abs bottom">
    <div class="abs copy">© 2014 HavenStead LLC. All rights reserved.</div>
    <div class="abs social" aria-label="Social links"><i></i><i></i><i></i></div>
  </div>
</body>
</html>
```